Velmo Swinger site - new website, blogsite and merchandise point, connection to tradeva

We are a well established Swingers Club in the North east of UK and already have an existing site. www.velmo-example.co.uk, BUT we have changed our logo and our information on the site needs to be updated.

We are changing our hosting site to Nimbrashost.example ,also wanting to start a blog which is linked to the club, plus we wish to sell a small exclusive range of Velmo linked merchandise which will also be available on Tradeva.

I have attached a pdf of the majority of the content. additionally we will provide pictures and a videoclip which should be able to be viewed by pc's, lap tops and mobile phones (the whole website must be fully accessible via phone).

The new site must be able to be updated by someone with medium computer knowledge (usually me), by no means expert. Updates will generally be new pictures and written information. The site must be able to be transferred to NimbrasHost.

Velmo is one of the countries leading clubs and emphasises friendliness, fun & safety for its members, we look after you to ensure your experience is the best we can offer. We are very proud of our reputation, built up over more than 10 years.

Target Market(s)

Swingers, dreamers & fantasists, alternative lifestyle people

Coding

Coded - Design and coding required

Number of Pages Required

5+ page

Font styles to use
Sans Serif

Colors
000000
ec1f27
fbfbfb
eeeeee
eaeaea

Requirements
Must have
• website with blog attached, link to tradeva & quidlo, ability to run videoclip and picture album and must be compatable to transfer easily to Nimbrashost and be updated by non-professional (who can learn)
• Straightforward & easy to navigate
• over 18 content page with enter button
Nice to have
• sexy site
• link to chirpster maybe
• black site would be nice with red or white writing
Should not have
• children and animals in anyway shape or form

```html
<!DOCTYPE html>
<html lang="en">
<head>
<meta charset="utf-8">
<title>Velmo – Swingers Club</title>
<link href="https://fonts.googleapis.com/css2?family=Lora:wght@400;700&family=Open+Sans:wght@400;600;700&display=swap" rel="stylesheet">
<style>
:root{
  --black:#000000;
  --red:#ec1f27;
  --red-deep:#a3141a;
  --white:#fbfbfb;
  --light:#eeeeee;
  --light-2:#eaeaea;
  --grey:#9a9a9a;
  --panel:rgba(255,255,255,.12);
  --serif:'Lora', Georgia, serif;
  --sans:'Open Sans', Arial, sans-serif;
}
*{box-sizing:border-box;margin:0;padding:0}
html,body{width:1200px;height:5187px;overflow:hidden;background:var(--black);color:var(--white);font-family:var(--sans)}
.page{position:relative;width:1200px;height:5187px}
.wrap{width:940px;margin:0 auto;position:relative}
section{position:relative;overflow:hidden;text-align:center}
.bg{position:absolute;inset:0;z-index:0}
section>.wrap{z-index:1}

/* header */
.site-header{height:97px;background:#0c0c0c;display:flex;align-items:center;justify-content:space-between;padding:0 131px}
.logo{font-family:var(--serif);font-size:38px;letter-spacing:3px;color:var(--white);display:flex;align-items:center;gap:10px}
.logo i{width:12px;height:12px;background:var(--red);display:block}
.nav{display:flex;gap:34px;font-family:var(--serif);font-size:14px}
.nav a{color:var(--light);text-decoration:none}
.nav a.active{border-bottom:2px solid var(--white)}

.login-bar{height:48px;display:flex}
.login-bar a{flex:1;display:flex;align-items:center;justify-content:center;gap:10px;font-family:var(--serif);font-size:15px;text-decoration:none;letter-spacing:.5px}
.login-bar .member{background:var(--light-2);color:#222}
.login-bar .join{background:#cfcfcf;color:#222}

/* hero */
.hero{height:470px;text-align:left}
.hero .bg{background:radial-gradient(ellipse at 62% 40%,#ff3a3a 0%,#c40d14 35%,#5e0206 75%,#1a0001 100%)}
.hero-copy{position:absolute;left:131px;top:140px;z-index:1}
.hero-copy h1{font-family:var(--serif);font-weight:400;font-size:25px;line-height:1.32;color:var(--white);width:330px}
.btn-outline{display:inline-block;border:1px solid var(--white);color:var(--white);font-family:var(--serif);font-size:14px;padding:9px 20px;text-decoration:none;letter-spacing:.5px}
.hero-copy .btn-outline{margin-top:18px}
.arrow{position:absolute;top:360px;width:26px;height:34px;background:rgba(0,0,0,.35);z-index:1;display:flex;align-items:center;justify-content:center}
.arrow.prev{left:0}.arrow.next{right:0}

/* section headings */
.section-title{display:inline-block;background:var(--red-deep);border:2px solid var(--red);font-family:var(--serif);font-size:22px;font-weight:400;letter-spacing:1px;padding:6px 24px;color:var(--white)}
.lead{font-family:var(--serif);font-weight:700;font-size:15px;margin-top:20px;line-height:1.55}
.body-text{font-size:12.5px;line-height:1.75;color:#cfcfcf;margin-top:14px}
.btn-pair{display:flex;justify-content:center;gap:30px;margin-top:22px}
.btn-pair .btn-outline{width:240px;padding:9px 0;border-color:#888;color:var(--light);font-family:var(--sans);font-size:12.5px}

/* welcome */
.welcome{height:613px;padding-top:188px}
.welcome .bg{background:radial-gradient(ellipse at 55% 15%,#4a4a4a 0%,#262626 40%,#121212 100%)}

/* diary */
.diary{height:1192px;padding-top:139px}
.diary .bg{background:radial-gradient(ellipse at 30% 10%,#3d3d3d 0%,#1e1e1e 45%,#0e0e0e 100%)}
.events{display:grid;grid-template-columns:repeat(3,300px);gap:20px;margin-top:26px;justify-content:center}
.events.two{grid-template-columns:repeat(2,300px);margin-top:34px}
.photo{display:block;width:100%}
.event .photo{height:190px}
.event .day{font-family:var(--serif);font-size:12px;margin-top:10px;color:var(--light)}
.event h3{font-family:var(--serif);font-weight:400;color:var(--red);font-size:19px;margin-top:8px;line-height:1.2}
.event .time{font-family:var(--serif);font-size:14px;font-weight:700}
.diary .body-text{margin-top:48px}
.diary .btn-outline{margin-top:40px;font-family:var(--sans);font-size:13px;padding:10px 28px;border-color:#bbb}

/* membership */
.membership{height:625px;padding-top:210px}
.membership .bg{background:radial-gradient(ellipse at 50% 20%,#5a5a5a 0%,#2b2b2b 40%,#0d0d0d 100%)}
.fees h3{font-family:var(--serif);font-weight:400;color:var(--red);font-size:19px;margin-top:12px}
.fees p{font-family:var(--serif);font-weight:700;font-size:15px;line-height:1.5}
.notice{background:var(--panel);padding:20px 40px;margin-top:24px;font-family:var(--serif);font-size:12.5px;line-height:1.7;color:#dcdcdc}

/* blog */
.blog{height:622px;padding-top:155px}
.blog .bg{background:radial-gradient(ellipse at 50% 40%,#3a3a3a 0%,#1a1a1a 50%,#080808 100%)}
.posts{display:grid;grid-template-columns:repeat(3,300px);gap:20px;margin-top:26px;text-align:left}
.post .photo{height:200px}
.post time{display:block;color:var(--red);font-size:12px;margin-top:12px}
.post p{font-size:12.5px;line-height:1.5;margin-top:6px;font-weight:600}
.post small{display:block;font-size:11px;color:var(--grey);margin-top:10px}

/* merchandise */
.merch{height:588px;padding-top:122px}
.merch .bg{background:radial-gradient(ellipse at 20% 30%,#333 0%,#151515 55%,#050505 100%)}
.products{display:grid;grid-template-columns:repeat(4,215px);gap:26px;margin-top:26px;text-align:left;justify-content:center}
.product .photo{height:215px}
.product h4{font-size:12.5px;font-weight:400;margin-top:8px}
.product .price{color:var(--red);font-size:12px}
.merch .btn-outline{margin-top:32px;font-family:var(--sans);font-size:13px;padding:9px 30px;border-color:#bbb}
.store-name{display:block;margin-top:10px;font-size:14px;color:var(--white);font-weight:600}

/* contact */
.contact{height:658px;padding-top:191px}
.contact .bg{background:radial-gradient(ellipse at 60% 20%,#3b3b3b 0%,#1a1a1a 50%,#0a0a0a 100%)}
.contact-form{margin-top:26px}
.row{display:grid;grid-template-columns:repeat(4,1fr);gap:24px}
.field{height:40px;border:1px solid #555;background:rgba(255,255,255,.04);color:#999;font-size:12px;text-align:left;padding:11px 14px}
.field.message{margin-top:18px}
.submit{display:inline-block;margin-top:20px;background:#d9d9d9;color:#222;font-size:12px;font-weight:700;padding:9px 24px}
.info-bar{margin-top:50px;background:rgba(255,255,255,.13);height:80px;display:flex;align-items:center;justify-content:space-between;padding:0 30px;font-size:12px;color:#ddd}
.info-bar span{display:flex;align-items:center;gap:8px}

/* newsletter */
.newsletter{height:87px;background:var(--red-deep);display:flex;align-items:center;justify-content:center;gap:40px}
.newsletter h2{font-family:var(--serif);font-weight:400;font-size:26px;display:flex;align-items:center;gap:12px}
.subscribe{display:flex}
.subscribe .email{width:220px;height:34px;background:var(--white);color:#777;font-size:12px;padding:9px 12px;text-align:left}
.subscribe .go{height:34px;background:var(--black);font-family:var(--serif);font-size:12px;padding:10px 14px}

/* footer */
.site-footer{height:187px;background:#0b0b0b;text-align:center;padding-top:30px}
.footer-links{font-size:11px;color:#ccc;display:flex;justify-content:center;gap:10px}
.copyright{font-size:11px;color:#999;margin-top:8px}
.social{display:flex;justify-content:center;gap:14px;margin-top:24px}
.social span{width:34px;height:34px;border:1px solid #bbb;border-radius:50%;display:block}
</style>
</head>
<body>
<div class="page">

<header class="site-header">
  <div class="logo">VELMO<i></i></div>
  <nav class="nav">
    <a class="active" href="#">Home</a><a href="#">Diary</a><a href="#">Club Membership</a><a href="#">FAQ</a><a href="#">Contact Us</a>
  </nav>
</header>

<div class="login-bar">
  <a class="member" href="#"><svg width="14" height="14" viewBox="0 0 14 14"><path d="M1 7h8M6 4l3 3-3 3M9 1h4v12H9" fill="none" stroke="#222" stroke-width="1.5"/></svg>MEMBER LOGIN</a>
  <a class="join" href="#"><svg width="14" height="14" viewBox="0 0 14 14"><rect x="1" y="2" width="10" height="11" fill="none" stroke="#222" stroke-width="1.4"/><path d="M5 9l7-7" stroke="#222" stroke-width="1.6"/></svg>JOIN NOW</a>
</div>

<section class="hero">
  <div class="bg" role="img" aria-label="Dancers silhouetted against red club lighting"></div>
  <div class="hero-copy">
    <h1>A TRUE SWINGERS CLUB WHERE YOU CAN MEET, SOCIALISE AND PLAY (IF YOU WANT.......)</h1>
    <a class="btn-outline" href="#">VIEW EVENTS</a>
  </div>
  <div class="arrow prev"><svg width="10" height="14" viewBox="0 0 10 14"><path d="M8 1L2 7l6 6" fill="none" stroke="#fff" stroke-width="2"/></svg></div>
  <div class="arrow next"><svg width="10" height="14" viewBox="0 0 10 14"><path d="M2 1l6 6-6 6" fill="none" stroke="#fff" stroke-width="2"/></svg></div>
</section>

<section class="welcome">
  <div class="bg" role="img" aria-label="Dim black and white club interior"></div>
  <div class="wrap">
    <h2 class="section-title">WELCOME TO VELMO</h2>
    <p class="lead">We are the best Swingers Club in the North East, and also voted No 2 club in the UK.</p>
    <p class="body-text">We have retained the coveted title of No 1 Swingers Club in the North East (a joint 1st place with our great friends "Harbour Lounge" London). This prestigious award has been given to us by a panel of "mystery voters" (swingers, singles &amp; couples) working with the publication called "Nights Out Weekly" a copy of which is available in reception.</p>
    <p class="body-text">Please see our Frequently Asked Questions and Membership pages for more information about the club and its facilities.</p>
    <div class="btn-pair"><a class="btn-outline" href="#">Frequently Asked Questions</a><a class="btn-outline" href="#">Membership</a></div>
  </div>
</section>

<section class="diary">
  <div class="bg" role="img" aria-label="Dark monochrome crowd on a dance floor"></div>
  <div class="wrap">
    <h2 class="section-title">DIARY</h2>
    <p class="lead">The usual nights are on and we are open, but please call if you need further information,<br>we only shut between Christmas &amp; New Years Eve.</p>
    <div class="events">
      <div class="event"><div class="photo" role="img" aria-label="Women partying under purple lights" style="background:linear-gradient(135deg,#3b1d5c,#b3338a 55%,#2a0f3a)"></div><p class="day">Wednesdays</p><h3>GREEDY GIRLS NIGHT</h3><p class="time">- 8pm till midnight</p></div>
      <div class="event"><div class="photo" role="img" aria-label="Group of dancers on stage" style="background:linear-gradient(135deg,#2a1a40,#c04a8a 50%,#3a2350)"></div><p class="day">2nd Thursday</p><h3>TRIBDS CLUB</h3><p class="time">- 5pm till midnight</p></div>
      <div class="event"><div class="photo" role="img" aria-label="Couple in a pink lit lounge" style="background:linear-gradient(135deg,#2a0a2a,#b0207a 55%,#3a0c30)"></div><p class="day">4th Thursday</p><h3>BI NIGHT</h3><p class="time">- 8pm till midnight</p></div>
    </div>
    <div class="events two">
      <div class="event"><div class="photo" role="img" aria-label="Man with two women posing" style="background:linear-gradient(135deg,#d9d4cf,#6e6460 55%,#2a2424)"></div><p class="day">Fridays</p><h3>FLIRTY FRIDAY, MIXED NIGHT</h3><p class="time">- 8pm till 1.30am</p></div>
      <div class="event"><div class="photo" role="img" aria-label="Couple embracing" style="background:linear-gradient(135deg,#3a2420,#b5736a 50%,#2a1614)"></div><p class="day">Saturdays</p><h3>COUPLES NIGHT</h3><p class="time">- 9pm till 1.30am</p></div>
    </div>
    <p class="body-text">Once a month on a Saturday we have a theme party, and new in 2017 we are trying a few Friday parties, we have a couple of No Knicks parties and a couple of Full Moon Parties, for all the details pick up a theme party guide when you come along, see the posters or look on lush circles for more info, or see our Theme Party Page.<br>Theme parties are very busy and quite a social night, we have a buffet, a prize for best dressed and usually we make vodka jellies, served by our lovely waitresses.<br>Sundays mid-day till 4pm is Men only sauna, no women, strictly no women (unless you TV/CD) allowed.....</p>
    <a class="btn-outline" href="#">READ MORE</a>
  </div>
</section>

<section class="membership">
  <div class="bg" role="img" aria-label="Monochrome crowd under stage lights"></div>
  <div class="wrap">
    <h2 class="section-title">VELMO MEMBERSHIP</h2>
    <div class="fees">
      <h3>ANNUAL MEMBERSHIP FEES</h3>
      <p>£30.00 per couple or single guy (this includes half price entry for your next two visits)<br>£10.00 per single girl.</p>
    </div>
    <p class="notice">Military and Emergency Service Personnel, both serving &amp; retired (proof required) are always £10 membership, ID renewal and half price entry. This must remind us though every time you come along. The hotel rooms and meals do not qualify for discounts.</p>
    <div class="btn-pair"><a class="btn-outline" href="#">Frequently Asked Questions</a><a class="btn-outline" href="#">Membership</a></div>
  </div>
</section>

<section class="blog">
  <div class="bg" role="img" aria-label="Dark party crowd background"></div>
  <div class="wrap">
    <h2 class="section-title">BLOG</h2>
    <div class="posts">
      <article class="post"><div class="photo" role="img" aria-label="Crowd at a concert" style="background:linear-gradient(135deg,#1a2a4a,#6a6aa0 50%,#1a1a2a)"></div><time>11 May, 2017</time><p>Pellentesque dignissim nec quam vitae tinci dunt. Curabitur consectetur efficitur odio, id tempor leo porta sit amet.</p><small>Aenean orci nunc, gravida nec dui luctus...</small></article>
      <article class="post"><div class="photo" role="img" aria-label="Stage with crowd and lights" style="background:linear-gradient(135deg,#2a2a3a,#8a7a6a 50%,#1a1a1a)"></div><time>11 May, 2017</time><p>Pellentesque dignissim nec quam vitae tinci dunt. Curabitur consectetur efficitur odio, id tempor leo porta sit amet.</p><small>Aenean orci nunc, gravida nec dui luctus...</small></article>
      <article class="post"><div class="photo" role="img" aria-label="Couple dancing" style="background:linear-gradient(135deg,#5a5a5a,#b0a8a0 50%,#3a3a3a)"></div><time>11 May, 2017</time><p>Pellentesque dignissim nec quam vitae tinci dunt. Curabitur consectetur efficitur odio, id tempor leo porta sit amet.</p><small>Aenean orci nunc, gravida nec dui luctus...</small></article>
    </div>
  </div>
</section>

<section class="merch">
  <div class="bg" role="img" aria-label="Dark sparkling background"></div>
  <div class="wrap">
    <h2 class="section-title">MERCHANDISE</h2>
    <div class="products">
      <div class="product"><div class="photo" role="img" aria-label="White branded T-shirt on wood" style="background:linear-gradient(135deg,#6a4a30,#d8d4cc 50%,#5a3a22)"></div><h4>Velmo T-Shirt</h4><p class="price">$00.00</p></div>
      <div class="product"><div class="photo" role="img" aria-label="Cigarette lighter with flame" style="background:linear-gradient(180deg,#2a1a10,#c88a40 45%,#6a6a6a)"></div><h4>Cigarette Lighter</h4><p class="price">$00.00</p></div>
      <div class="product"><div class="photo" role="img" aria-label="Cigars in a box" style="background:linear-gradient(135deg,#e8d0a0,#a0683a 50%,#5a3218)"></div><h4>Cigars</h4><p class="price">$00.00</p></div>
      <div class="product"><div class="photo" role="img" aria-label="Woman with hookah smoke" style="background:linear-gradient(135deg,#f2eee8,#9a8a80 55%,#3a3030)"></div><h4>Hookah</h4><p class="price">$00.00</p></div>
    </div>
    <a class="btn-outline" href="#">VIEW ALL</a>
    <span class="store-name">tradeva</span>
  </div>
</section>

<section class="contact">
  <div class="bg" role="img" aria-label="Dark crowd with raised hands"></div>
  <div class="wrap">
    <h2 class="section-title">CONTACT US</h2>
    <div class="contact-form">
      <div class="row"><div class="field">Name</div><div class="field">Email</div><div class="field">Phone</div><div class="field">Age</div></div>
      <div class="field message">Message</div>
      <span class="submit">SUBMIT</span>
    </div>
    <div class="info-bar">
      <span><svg width="10" height="14" viewBox="0 0 10 14"><path d="M5 13C2 9 1 7 1 5a4 4 0 0 1 8 0c0 2-1 4-4 8z" fill="#ddd"/></svg>24 Building name, Street name, City - Zipcode</span>
      <span><svg width="12" height="12" viewBox="0 0 12 12"><path d="M2 1l3 2-1 2 3 3 2-1 2 3-2 1C5 11 1 7 1 3z" fill="#ddd"/></svg>Phone : 0700 000 1234</span>
      <span><svg width="14" height="10" viewBox="0 0 14 10"><rect x=".5" y=".5" width="13" height="9" fill="none" stroke="#ddd"/><path d="M1 1l6 5 6-5" fill="none" stroke="#ddd"/></svg>Email : velmoswingers@mailbox.example</span>
    </div>
  </div>
</section>

<section class="newsletter">
  <h2><svg width="26" height="18" viewBox="0 0 26 18"><rect x="1" y="1" width="24" height="16" fill="none" stroke="#fbfbfb" stroke-width="2"/><path d="M1 1l12 9 12-9" fill="none" stroke="#fbfbfb" stroke-width="2"/></svg>NEWSLETTER SUBSCRIBE</h2>
  <div class="subscribe"><span class="email">Email address</span><span class="go">SUBSCRIBE NOW</span></div>
</section>

<footer class="site-footer">
  <div class="footer-links"><span>Home</span>|<span>Diary</span>|<span>Club Membership</span>|<span>FAQ</span>|<span>Contact Us</span></div>
  <p class="copyright">Copyright © 2017 Velmo - All rights reserved</p>
  <div class="social"><span aria-label="Social link"></span><span aria-label="Social link"></span><span aria-label="Social link"></span></div>
</footer>

</div>
</body>
</html>
```